Web Design

We need a website for a company based in Doha Qatar called
Lumara Maid Service.

It is the number one maid cleaning service company, and we have branches all over qatar.

Luxury Cleaning Service Provider.

The color scheme is gold, yellow and black like the logo.

Before they get to the website, there is an intro video.

The website should depict luxury.

Target Market(s)

People who need maids at their houses.

Industry/Entity Type

Cleaning Service

Requirements
Must have
• Luxury, Sleek, Modern

The opening sequence is a video which I already have. Its too big to upload here so I am going to put it on youtube.

After the opening sequence, the home page should have a widescreen photo background and it should change every five seconds, the first background photo should be of qatar westbay skyline. Then the second background should be of maid photos in cleaning positions. Then the third background should be of cleaner photos etc.

We will send you all the tabs and all the content later.

```html
<!DOCTYPE html>
<html lang="en">
<head>
<meta charset="utf-8">
<title>Lumara Maid Service</title>
<link rel="stylesheet" href="https://fonts.googleapis.com/css2?family=Bebas+Neue&family=Open+Sans:wght@400;600&family=Oxygen:wght@400&display=swap">
<style>
  :root {
    --yellow: #fff77a;
    --gold: #c9962e;
    --black: #000000;
    --ink: #1a1a1a;
    --white: #ffffff;
    --player-bar: #1c1c1c;
    --volume-blue: #2aa7de;
    --sky-top: #5e6d8a;
    --sky-mid: #8b96a8;
    --water: #4a4f52;
  }
  * { box-sizing: border-box; margin: 0; padding: 0; }
  html, body { width: 1200px; height: 800px; overflow: hidden; }
  body { position: relative; font-family: "Open Sans", sans-serif; background: var(--white); color: var(--ink); }

  /* Header */
  .site-header { position: absolute; top: 0; left: 0; width: 1200px; height: 100px; background: var(--white); }
  .brand { position: absolute; left: 100px; top: 36px; display: flex; align-items: center; gap: 8px; }
  .brand-dot { width: 14px; height: 14px; border-radius: 50%; background: var(--gold); }
  .brand-name { font-family: "Open Sans", sans-serif; font-weight: 600; font-size: 17px; color: var(--gold); letter-spacing: 0.3px; }
  .main-nav { position: absolute; top: 33px; left: 524px; display: flex; }
  .main-nav a { display: block; height: 42px; line-height: 42px; padding: 0 20px; font-size: 14px; color: var(--ink); text-decoration: none; border-radius: 4px; margin-right: 16px; }
  .main-nav a.is-active { background: var(--yellow); }

  /* Hero */
  .hero { position: absolute; top: 100px; left: 0; width: 1200px; height: 600px; overflow: hidden; }
  .hero-backdrop { position: absolute; inset: 0;
    background: linear-gradient(180deg, var(--sky-top) 0%, #7683a0 30%, var(--sky-mid) 55%, #6f7676 72%, var(--water) 100%); }
  .hero-title { position: absolute; left: 100px; top: 188px; font-family: "Bebas Neue", sans-serif; font-size: 46px; line-height: 48px; color: var(--yellow); letter-spacing: 0.5px; }
  .hero-text { position: absolute; left: 100px; top: 252px; width: 520px; font-size: 18px; line-height: 30px; color: var(--white); }
  .hero-button { position: absolute; left: 100px; top: 364px; width: 134px; height: 54px; background: var(--yellow); font-family: "Bebas Neue", sans-serif; font-size: 23px; line-height: 56px; text-align: center; color: var(--black); text-decoration: none; }
  .slide-arrow { position: absolute; width: 28px; height: 40px; }
  .slide-arrow.prev { left: 42px; top: 287px; }
  .slide-arrow.next { left: 1130px; top: 290px; }

  /* Video */
  .video-player { position: absolute; left: 636px; top: 144px; width: 464px; height: 302px; box-shadow: 0 14px 18px -8px rgba(0,0,0,0.55); }
  .video-title { height: 26px; background: var(--player-bar); color: var(--white); font-size: 12px; line-height: 26px; padding-left: 7px; }
  .video-frame { position: relative; height: 276px; background: linear-gradient(135deg, #e6e4e2 0%, #c9ccd6 40%, #a7b2c9 70%, #d9dbe0 100%); }
  .player-play { position: absolute; left: 27px; top: 219px; width: 68px; height: 43px; background: rgba(40,40,40,0.85); border-radius: 3px; }
  .player-bar { position: absolute; left: 106px; top: 227px; width: 336px; height: 35px; background: rgba(40,40,40,0.85); border-radius: 3px; }
  .player-track { position: absolute; left: 11px; top: 12px; width: 245px; height: 12px; border: 1px solid #d8d8d8; }
  .player-volume { position: absolute; left: 266px; top: 10px; }
  .player-fullscreen { position: absolute; left: 312px; top: 10px; }

  .slide-dots { position: absolute; left: 1026px; top: 575px; display: flex; gap: 8px; }
  .slide-dots span { width: 14px; height: 14px; border-radius: 50%; background: #e8e8e8; border: 2px solid #555; }
  .slide-dots span.is-active { background: var(--yellow); border-color: #d8cd4a; }

  /* Footer */
  .site-footer { position: absolute; top: 700px; left: 0; width: 1200px; height: 100px; background: var(--black); color: var(--white); font-family: "Oxygen", sans-serif; }
  .footer-nav { position: absolute; left: 98px; top: 23px; font-size: 17px; }
  .footer-nav a { color: var(--white); text-decoration: none; }
  .footer-nav .sep { margin: 0 8px; }
  .copyright { position: absolute; left: 98px; top: 58px; font-size: 13px; }
  .social-links { position: absolute; left: 978px; top: 38px; display: flex; gap: 8px; }
  .social-links span { width: 24px; height: 24px; border-radius: 3px; }
  .social-a { background: #3b5b98; }
  .social-b { background: #3fb3e6; }
  .social-c { background: #1f76b0; }
  .social-d { background: #f28a1c; }
</style>
</head>
<body>
  <header class="site-header">
    <div class="brand">
      <span class="brand-dot"></span>
      <span class="brand-name">Lumara Maid Service</span>
    </div>
    <nav class="main-nav">
      <a href="#" class="is-active">Home</a>
      <a href="#">About Us</a>
      <a href="#">Services</a>
      <a href="#">Testimonals</a>
      <a href="#">Contact Us</a>
    </nav>
  </header>

  <section class="hero">
    <div class="hero-backdrop" role="img" aria-label="Blurred Doha West Bay skyline over the water"></div>

    <svg class="slide-arrow prev" viewBox="0 0 28 40" aria-hidden="true">
      <path d="M22 3 L6 20 L22 37" fill="none" stroke="#ffffff" stroke-width="7" stroke-linejoin="round"/>
    </svg>
    <svg class="slide-arrow next" viewBox="0 0 28 40" aria-hidden="true">
      <path d="M6 3 L22 20 L6 37" fill="none" stroke="#ffffff" stroke-width="7" stroke-linejoin="round"/>
    </svg>

    <h1 class="hero-title">Lorem ipsum dolor sit amet</h1>
    <p class="hero-text">Nulla consequat massa quis enim. Donec pede justo, fringilla vel, aliquet nec, vulputate eget, arcu. In enim justo, rhoncus ut, imperdiet a, venenatis vitae, justo.</p>
    <a href="#" class="hero-button">Read More +</a>

    <div class="video-player">
      <div class="video-title">Cleaning</div>
      <div class="video-frame" role="img" aria-label="Video still of a maid in gloves holding a spray bottle">
        <div class="player-play">
          <svg width="68" height="43" viewBox="0 0 68 43" aria-hidden="true"><path d="M27 13 L43 21.5 L27 30 Z" fill="#ffffff"/></svg>
        </div>
        <div class="player-bar">
          <div class="player-track"></div>
          <svg class="player-volume" width="38" height="14" viewBox="0 0 38 14" aria-hidden="true">
            <g fill="var(--volume-blue)">
              <rect x="0" y="0" width="3" height="14"/><rect x="5" y="0" width="3" height="14"/>
              <rect x="10" y="0" width="3" height="14"/><rect x="15" y="0" width="3" height="14"/>
              <rect x="20" y="0" width="3" height="14"/><rect x="25" y="0" width="3" height="14"/>
              <rect x="30" y="0" width="3" height="14"/><rect x="35" y="0" width="3" height="14"/>
            </g>
          </svg>
          <svg class="player-fullscreen" width="15" height="15" viewBox="0 0 15 15" aria-hidden="true">
            <g fill="none" stroke="#ffffff" stroke-width="2.4">
              <path d="M1 5V1h4M10 1h4v4M14 10v4h-4M5 14H1v-4"/>
            </g>
          </svg>
        </div>
      </div>
    </div>

    <div class="slide-dots">
      <span class="is-active"></span><span></span><span></span>
    </div>
  </section>

  <footer class="site-footer">
    <nav class="footer-nav">
      <a href="#">Home</a><span class="sep">|</span><a href="#">About Us</a><span class="sep">|</span><a href="#">Services</a><span class="sep">|</span><a href="#">Products</a><span class="sep">|</span><a href="#">Contact Us</a><span class="sep">|</span><a href="#">Blog</a>
    </nav>
    <p class="copyright">© 2014 Company Name&nbsp; All right reserved&nbsp; Term of Use</p>
    <div class="social-links">
      <span class="social-a"></span><span class="social-b"></span><span class="social-c"></span><span class="social-d"></span>
    </div>
  </footer>
</body>
</html>
```